New hardcover book cover

I want a striking, eye-catching cover with title, subtitle and a picture.See for previous book covers: www.brightquillpress.com

Target Market(s)

young, successful entrepreneurs that have built a business in a niche market that they discovered.

Font styles to use
Serif

Colors

Designer to choose colors to be used in the design.

Requirements
Must have
• A book cover that impresses and captures the imagination of those who look at it.
• MY MISTAKE, SORRY.
• Title: Founders Behind the Quiet Trade Boom
• Subtitle: 25 stories of success from
• discovering hidden opportunities
• Author: Dennis Harlow
• Please use the photo attached, thanks.

```html
<!DOCTYPE html>
<html lang="en">
<head>
<meta charset="utf-8">
<title>Founders Behind the Quiet Trade Boom — Dennis Harlow</title>
<link href="https://fonts.googleapis.com/css2?family=Bebas+Neue&family=Montserrat:wght@300;400&display=swap" rel="stylesheet">
<style>
  :root {
    --ink-navy: #1c2130;
    --ink-deep: #12151f;
    --target-pink: #c41f57;
    --title-pink: #c8245c;
    --flame-orange: #f29a2e;
    --steel-grey: #8c93a3;
    --paper-white: #f4f4f4;
  }
  * { margin: 0; padding: 0; box-sizing: border-box; }
  html, body { width: 764px; height: 1200px; overflow: hidden; background: var(--ink-deep); }
  .cover {
    position: relative;
    width: 764px;
    height: 1200px;
    overflow: hidden;
    background: var(--ink-navy);
  }
  .cover-photo {
    position: absolute;
    inset: 0;
    background:
      radial-gradient(ellipse 260px 380px at 90px 500px, rgba(196,31,87,0.95), rgba(196,31,87,0) 100%),
      radial-gradient(ellipse 300px 260px at 380px 160px, rgba(242,154,46,0.85), rgba(242,154,46,0) 100%),
      radial-gradient(ellipse 320px 420px at 620px 520px, rgba(140,147,163,0.55), rgba(140,147,163,0) 100%),
      linear-gradient(180deg, #2a2f3e 0%, var(--ink-navy) 55%, var(--ink-deep) 100%);
  }
  .author {
    position: absolute;
    top: 58px;
    left: 0;
    width: 100%;
    text-align: center;
    font-family: "Montserrat", sans-serif;
    font-weight: 300;
    font-size: 47px;
    letter-spacing: 0.2em;
    text-indent: 0.2em;
    color: var(--paper-white);
  }
  .title {
    position: absolute;
    left: 0;
    top: 676px;
    width: 100%;
    font-family: "Bebas Neue", sans-serif;
    color: var(--paper-white);
    text-align: center;
    line-height: 1;
  }
  .title-line { display: block; }
  .title-founders { font-size: 86px; }
  .title-quiet {
    display: flex;
    justify-content: center;
    align-items: center;
    gap: 8px;
    margin-top: -4px;
  }
  .title-small-stack {
    display: flex;
    flex-direction: column;
    font-size: 40px;
    line-height: 0.95;
    text-align: right;
  }
  .title-quiet-word { font-size: 122px; }
  .title-trade {
    display: flex;
    justify-content: center;
    align-items: center;
    gap: 30px;
    font-size: 112px;
    margin-top: -14px;
  }
  .title-rule {
    width: 68px;
    height: 7px;
    background: var(--paper-white);
  }
  .title-boom {
    font-size: 130px;
    color: var(--title-pink);
    margin-top: -16px;
  }
  .subtitle {
    position: absolute;
    left: 0;
    top: 1086px;
    width: 100%;
    text-align: center;
    font-family: "Montserrat", sans-serif;
    font-weight: 400;
    font-size: 23px;
    line-height: 34px;
    color: var(--paper-white);
    text-transform: uppercase;
  }
</style>
</head>
<body>
  <main class="cover">
    <div class="cover-photo" role="img" aria-label="Photo of a flaming dart striking the centre of a pink and grey dartboard"></div>

    <p class="author">DENNIS HARLOW</p>

    <h1 class="title">
      <span class="title-line title-founders">FOUNDERS</span>
      <span class="title-line title-quiet">
        <span class="title-small-stack"><span>BEHIND</span><span>THE</span></span>
        <span class="title-quiet-word">QUIET</span>
      </span>
      <span class="title-line title-trade">
        <span class="title-rule"></span>
        <span>TRADE</span>
        <span class="title-rule"></span>
      </span>
      <span class="title-line title-boom">BOOM</span>
    </h1>

    <p class="subtitle">25 captivating stories of success<br>from discovering hidden opportunities</p>
  </main>
</body>
</html>
```